Oversized Postcard Designer

Oversized( 8.52 by 4.57) handout postcards.
We need promotional post cards that our congregation can use to pass out to their frineds and family for a special Spring Break Revival. I attempted to create "something" but was not completely satisfied with it. I have included my attempt in the uploaded images.
Trhe front part of the post card I would like for it to capture the attention of people. The Backside of the postcard can contain event information.
About the Event Information.
Spring Break Revival
Special Guest: Dale Whitcombe (www.dalewhitcombe.example)
Dates: Sunday March 15 thru Wednesday March 18
Times: Sunday 9:00 a.m., 11:00 a.m., and 6:00 p.m.
Monday - Wednesday 6:00 p.m. with a free meal being served at 5:00 p.m.
Our Location is 418 N. Larkspur Street, Independence, KS 67399
Our Phone Number 620-555-0147

```html
<!DOCTYPE html>
<html lang="en">
<head>
<meta charset="utf-8">
<title>Spring Break Revival – Postcard Design</title>
<link rel="stylesheet" href="https://fonts.googleapis.com/css2?family=Cinzel:wght@400;700&family=Cinzel+Decorative:wght@700&display=swap">
<style>
  :root {
    --page: #ffffff;
    --ink-blue: #1d3f78;
    --deep-blue: #0b2f5c;
    --band-blue: #0f4d92;
    --band-dark: #06213f;
    --sky-light: #e9f1f9;
    --sky-mid: #b7cfe6;
    --accent-orange: #e8742c;
    --white: #ffffff;
    --logo-grey: #2a2a2a;
  }
  * { box-sizing: border-box; margin: 0; padding: 0; }
  html, body { width: 1200px; height: 1000px; overflow: hidden; background: var(--page); }
  body { position: relative; font-family: "Cinzel", serif; }

  .section-title {
    position: absolute; left: 960px; top: 58px;
    color: var(--ink-blue); font-size: 28px; line-height: 35px; letter-spacing: 0.5px;
  }

  .card {
    position: absolute; left: 330px; width: 570px; height: 443px;
    overflow: hidden; box-shadow: 3px 5px 10px rgba(0,0,0,0.35);
  }
  .card--front { top: 57px; background: linear-gradient(180deg, var(--white) 0%, var(--white) 30%, var(--sky-light) 55%, var(--sky-mid) 85%); }
  .card--back { top: 530px; }

  .splash {
    position: absolute; left: 0; top: 0; width: 570px; height: 40px;
    background: linear-gradient(180deg, rgba(30,100,170,0.75), rgba(30,100,170,0));
  }
  .photo-front {
    position: absolute; left: 110px; top: 40px; width: 225px; height: 320px;
    background: radial-gradient(ellipse at 50% 45%, #e8ddd0 0%, #c6b7a4 45%, #8a96a6 80%, rgba(140,155,175,0) 100%);
  }
  .rock-ledge {
    position: absolute; left: 0; top: 255px; width: 570px; height: 120px;
    background: linear-gradient(180deg, rgba(120,120,115,0) 0%, rgba(120,120,115,0.55) 40%, rgba(90,95,100,0.6) 100%);
  }
  .brand-name {
    position: absolute; font-family: "Cinzel", serif; font-weight: 700;
    font-size: 17px; letter-spacing: 0.3px;
  }
  .card--front .brand-name { left: 30px; top: 28px; color: var(--logo-grey); }
  .card--back .brand-name { left: 22px; top: 34px; color: rgba(255,255,255,0.7); }

  .story {
    position: absolute; left: 346px; top: 82px; color: var(--ink-blue);
    font-size: 13.5px; line-height: 22.5px; white-space: nowrap;
  }
  .story .until { margin-top: 10px; }

  .front-band { position: absolute; left: 0; top: 0; }

  .church-mark {
    position: absolute; display: flex; align-items: center; gap: 8px;
    color: var(--white); font-size: 13px; line-height: 16px;
  }
  .church-mark__square { width: 12px; height: 12px; background: currentColor; flex: none; }
  .card--front .church-mark { left: 438px; top: 282px; width: 100px; }
  .card--back .church-mark { left: 20px; top: 384px; width: 200px; color: rgba(255,255,255,0.65); font-size: 17px; line-height: 20px; }

  .kicker { font-size: 17px; color: var(--white); letter-spacing: 0.5px; }
  .revival { font-family: "Cinzel Decorative", serif; font-weight: 700; color: var(--white); font-size: 44px; line-height: 46px; }
  .front-title { position: absolute; left: 32px; top: 328px; }
  .featuring-line { position: absolute; left: 32px; top: 403px; color: var(--white); }
  .featuring-line small { font-size: 11px; margin-right: 12px; }
  .featuring-line em { font-size: 17px; font-style: italic; }
  .front-dates { position: absolute; right: 20px; top: 402px; color: var(--white); font-size: 17px; }
  sup { font-size: 0.55em; }

  .photo-back {
    position: absolute; inset: 0;
    background:
      radial-gradient(ellipse 240px 330px at 70px 210px, rgba(120,170,215,0.85), rgba(60,120,180,0) 100%),
      linear-gradient(135deg, #2c6aa6 0%, #0f4478 45%, #0a3561 100%);
  }
  .event-info {
    position: absolute; left: 190px; width: 380px; top: 28px;
    text-align: center; color: var(--white); font-size: 14px; line-height: 20.5px;
  }
  .event-info .revival { margin-bottom: 18px; }
  .guest-label { color: var(--accent-orange); font-size: 13px; }
  .guest-featuring { color: var(--accent-orange); font-size: 17px; }
  .guest-name { color: var(--accent-orange); font-size: 23px; font-style: italic; line-height: 32px; margin-bottom: 8px; }
  .address { font-size: 13px; white-space: nowrap; }
  .gap { height: 20px; }
</style>
</head>
<body>

<div class="section-title">Postcard<br>Design</div>

<section class="card card--front">
  <div class="splash" role="img" aria-label="Blue watercolour splash along the top edge"></div>
  <div class="rock-ledge" role="img" aria-label="Stone ledge the speaker is seated on"></div>
  <div class="photo-front" role="img" aria-label="Photo of the speaker seated, hands clasped in prayer"></div>
  <div class="brand-name">Whitcombe Ministries</div>

  <div class="story">
    He had nine step-fathers,<br>
    an alcoholic mother,<br>
    was abused &amp; neglected,<br>
    left without hope.
    <div class="until">Until ....</div>
  </div>

  <svg class="front-band" width="570" height="443" viewBox="0 0 570 443" aria-hidden="true">
    <defs>
      <linearGradient id="bandFill" x1="0" y1="0" x2="0" y2="1">
        <stop offset="0" stop-color="#1b6cb8"/>
        <stop offset="0.6" stop-color="#0d4486"/>
        <stop offset="1" stop-color="#06213f"/>
      </linearGradient>
    </defs>
    <polygon points="0,332 100,290 430,352 570,340 570,443 0,443" fill="#2f7cc4" opacity="0.6"/>
    <polygon points="0,338 100,298 430,360 570,350 570,443 0,443" fill="url(#bandFill)"/>
    <rect x="428" y="235" width="120" height="150" fill="#0d3f78" opacity="0.85"/>
  </svg>

  <div class="church-mark"><span class="church-mark__square"></span><span>Larkspur Baptist Independence</span></div>

  <div class="front-title">
    <div class="kicker">Spring Break</div>
    <div class="revival">Revival</div>
  </div>
  <div class="featuring-line"><small>featuring</small><em>Dale Whitcombe</em></div>
  <div class="front-dates">On March 15<sup>th</sup> – 18<sup>th</sup></div>
</section>

<section class="card card--back">
  <div class="photo-back" role="img" aria-label="Blue-toned photo of the speaker smiling, in front of a church interior"></div>
  <div class="brand-name">Whitcombe Ministries</div>

  <div class="event-info">
    <div class="kicker">Spring Break</div>
    <div class="revival">Revival</div>
    <div class="guest-label">Special Guest:</div>
    <div class="guest-featuring">Featuring</div>
    <div class="guest-name">Dale Whitcombe</div>
    <div>On</div>
    <div>Sunday, March 15<sup>th</sup></div>
    <div>thru</div>
    <div>Wednesday March 18<sup>th</sup></div>
    <div class="gap"></div>
    <div>Sunday 9:00 a.m., 11:00 a.m., 6:00 p.m.</div>
    <div>Monday - Wednesday 6:00 p.m.</div>
    <div class="gap"></div>
    <div>free meal will be served at 5:00 p.m.</div>
    <div>At</div>
    <div class="address">418 N. Larkspur Street, Independence, KS 67399</div>
  </div>

  <div class="church-mark"><span class="church-mark__square"></span><span>Larkspur Baptist Independence</span></div>
</section>

</body>
</html>
```